Holiday Rental Company Flyer Design (DL not A5)

Note from Brandloom Administration: The category sizing selected is A5, however the project requires DL sized artwork. Please refer to the DL template link below while the 'Special Requirements' are updated accordingly.

Project Brief:
We need a double sided DL flyer designed for an up market Holiday Rental Company that portrays a personalised approach to property management. These are to be used for letter box drops to homes we're specifically targeting so the design should be modern, complimentary colour palette, uncluttered & visually appealing.

Please Download the DL Template from Quillora here: http://www.quillora.com.au/ql/ns/propath/UploadResources.aspx?selectedTab=0?pfid=KMT&pf_id=KMT&xnav=easypath-upload-image#Templates

Target Market(s)

Wealthy Home Owners

Industry/Entity Type

It Company

Other font styles liked:
• Avant Garde Extra Light & Demi

Colors
33b8a4

Requirements
Must have
• DL Flyer sizes (210mm width x 99mm width, plus 3mm bleed)
• Front: Logo, Main Image & Grab
• Back: Contact Details & Brief Description of our business
• Images: Ideally the main image should be the house with the pool but alternatively a lifestyle images could also be used.
Nice to have
• A creative designer!
Should not have
• Clutter & busy designs

```html
<!DOCTYPE html>
<html lang="en">
<head>
<meta charset="utf-8">
<title>Coastline Retreats – DL Flyer</title>
<link rel="stylesheet" href="https://fonts.googleapis.com/css2?family=Poppins:wght@200;300;700&display=swap">
<style>
  :root {
    --backdrop: #3b2518;
    --mint: #45f47e;
    --ink: #161616;
    --paper: #ffffff;
    --night: #1f1f6e;
    --pool: #3f7ee8;
    --warm: #b89a6a;
    --bed-top: #d9c7a8;
    --bed-bottom: #d8d04a;
  }
  * { box-sizing: border-box; margin: 0; padding: 0; }
  html, body { width: 1200px; height: 900px; overflow: hidden; }
  body {
    background: var(--backdrop);
    position: relative;
    font-family: "Poppins", sans-serif;
    color: var(--ink);
  }
  .panel {
    position: absolute;
    top: 0;
    width: 435px;
    height: 900px;
    background: var(--paper);
    overflow: hidden;
  }
  .panel--front { left: 114px; }
  .panel--back { left: 652px; background: var(--mint); }

  /* Front */
  .brand-block {
    height: 290px;
    background: var(--mint);
    display: flex;
    flex-direction: column;
    align-items: center;
    padding-top: 62px;
  }
  .brand-name {
    font-weight: 200;
    font-size: 44px;
    line-height: 50px;
    letter-spacing: 3px;
    color: var(--paper);
    text-align: center;
  }
  .brand-dot {
    margin-top: 26px;
    width: 44px;
    height: 44px;
    border: 1.5px solid var(--paper);
    border-radius: 50%;
  }
  .hero-photo {
    position: absolute;
    top: 298px;
    left: 0;
    width: 435px;
    height: 302px;
    background:
      linear-gradient(to bottom, transparent 70%, var(--pool) 88%, #6bc4f4 100%),
      linear-gradient(100deg, var(--warm) 0%, #5b4a4a 40%, var(--night) 60%, #2a2aa0 100%);
  }
  .front-grab {
    position: absolute;
    top: 660px;
    left: 0;
    width: 435px;
    text-align: center;
    font-weight: 700;
    font-size: 31px;
    line-height: 40px;
    color: var(--mint);
    letter-spacing: 0.3px;
  }

  /* Back */
  .lifestyle-photo {
    height: 290px;
    background:
      linear-gradient(to bottom, var(--bed-top) 0%, #e8ddc6 35%, var(--bed-bottom) 60%, #e4643f 85%, #4fc2a8 100%);
  }
  .back-heading {
    margin-top: 28px;
    text-align: center;
    font-weight: 700;
    font-size: 24px;
    letter-spacing: 0.3px;
  }
  .intro {
    margin: 30px 40px 0 36px;
    font-weight: 300;
    font-size: 13.4px;
    line-height: 16px;
    text-align: justify;
  }
  .intro + .intro { margin-top: 16px; }
  .intro strong { font-weight: 700; }
  .benefits {
    list-style: none;
    margin: 50px 56px 0;
    text-align: center;
    font-weight: 300;
    font-size: 16px;
    line-height: 20px;
  }
  .benefits li { padding: 8px 0 10px; }
  .benefits li + li { border-top: 1px solid rgba(255,255,255,0.8); }
  .contact-lead {
    position: absolute;
    top: 760px;
    left: 40px;
    right: 40px;
    font-weight: 300;
    font-size: 11.5px;
    line-height: 14px;
  }
  .contact-list {
    position: absolute;
    top: 800px;
    left: 0;
    width: 435px;
    list-style: none;
    font-weight: 300;
    font-size: 11px;
    line-height: 14px;
    text-align: center;
  }
  .contact-list li { display: flex; justify-content: center; align-items: center; gap: 4px; }
  .contact-list svg { width: 9px; height: 9px; fill: var(--paper); }
</style>
</head>
<body>
  <section class="panel panel--front">
    <header class="brand-block">
      <h1 class="brand-name">COASTLINE<br>RETREATS</h1>
      <span class="brand-dot" aria-hidden="true"></span>
    </header>
    <div class="hero-photo" role="img" aria-label="Luxury home with lit lap pool at dusk"></div>
    <p class="front-grab">HOLIDAY RENTAL<br>MANAGEMENT WITH<br>A DIFFERENCE</p>
  </section>

  <section class="panel panel--back">
    <div class="lifestyle-photo" role="img" aria-label="Bedroom with yellow cushions on a colourful geometric quilt"></div>
    <h2 class="back-heading">WHAT WE DO DIFFERENTLY!</h2>
    <p class="intro">Rather than relying upon a key safe or a central pick-up destination, a ‘Coastline Retreats’ staff member will greet guests upon arrival.</p>
    <p class="intro">Our ‘<strong>Meet &amp; Greet</strong>’ service provides home owners with an increased level of Security and also allows us to:</p>
    <ul class="benefits">
      <li>Prepare the home for their arrival<br>(lights, heaters, music etc.)</li>
      <li>Establish a rapport &amp; help facilitate<br>future bookings</li>
      <li>Reiterate their responsibilities to ensure<br>the return of their bond</li>
    </ul>
    <p class="contact-lead">If you’d like to know what your property could achieve or require additional information, please contact us on:</p>
    <ul class="contact-list">
      <li><svg viewBox="0 0 10 10"><path d="M2 0h2l1 3-1.5 1a6 6 0 0 0 2.5 2.5L7 5l3 1v2c0 1-1 2-2 2A8 8 0 0 1 0 2c0-1 1-2 2-2z"/></svg>: (03)5900 4127</li>
      <li><svg viewBox="0 0 10 10"><path d="M0 2h10v6H0zM0 2l5 3.5L10 2" stroke="#45f47e" stroke-width="0.8"/></svg>stay@coastlineretreats.com.au</li>
      <li><svg viewBox="0 0 10 10"><circle cx="5" cy="5" r="5"/></svg>coastlineretreats.com.au</li>
      <li><svg viewBox="0 0 10 10"><path d="M5 0a3.5 3.5 0 0 1 3.5 3.5C8.5 6 5 10 5 10S1.5 6 1.5 3.5A3.5 3.5 0 0 1 5 0z"/></svg>PO Box 18, Tidewater Victoria 3950</li>
    </ul>
  </section>
</body>
</html>
```